Business Card Design

New business card design

Target Market(s)

Residential & Commercial Property Managers

Industry/Entity Type

Plumbing Services

Contact Information for Business Card

Name - Rowan Keddle, title - Director, Phone Number - 0431 286 517, email - rowan@tbk-plumbing.com.au, Company ABN - 73 215 904 386,

Font styles to use
Sans Serif

Colors
0054AA
0677BA
7BADD7
CADEEF
E8F1F8

```html
<!DOCTYPE html>
<html lang="en">
<head>
<meta charset="utf-8">
<title>Business Card – Rowan Keddle, Director</title>
<link rel="stylesheet" href="https://fonts.googleapis.com/css2?family=Lexend:wght@400;700&family=Poppins:wght@400;500&display=swap">
<style>
  :root {
    --backdrop: #c4c4c4;
    --card-dark: #1f232a;
    --card-light: #fbfbfc;
    --accent: #14a0e6;
    --accent-deep: #0677ba;
    --accent-bright: #00d9ff;
    --accent-top: #0054aa;
    --ink-light: #ffffff;
    --ink-dark: #1c2530;
    --ink-muted: #5a5f66;
  }
  * { box-sizing: border-box; margin: 0; padding: 0; }
  html, body {
    width: 1200px; height: 950px; overflow: hidden;
    background: var(--backdrop);
  }
  .canvas { position: relative; width: 1200px; height: 950px; }

  .card {
    position: absolute; left: 296px; width: 608px; height: 347px;
    overflow: hidden;
  }
  .card--front { top: 105px; background: var(--card-dark); }
  .card--back  { top: 501px; background: var(--card-light); }

  .brand-art {
    position: absolute; border-radius: 50%;
    background: radial-gradient(circle at 45% 70%, var(--accent-bright) 0%, var(--accent) 55%, var(--accent-top) 100%);
  }
  .card--front .brand-art { left: 66px; top: 122px; width: 130px; height: 130px; }
  .card--back .brand-art  { left: 382px; top: 112px; width: 156px; height: 156px; }

  .person-name {
    position: absolute; left: 263px; top: 52px;
    font-family: "Lexend", sans-serif; font-size: 37px; line-height: 1;
    letter-spacing: -0.5px; color: var(--ink-light); font-weight: 400;
    white-space: nowrap;
  }
  .person-name .first { color: var(--accent); font-weight: 700; }
  .person-title {
    position: absolute; left: 264px; top: 97px;
    font-family: "Lexend", sans-serif; font-size: 10px;
    letter-spacing: 5.2px; color: var(--ink-light);
  }

  .contact-pill {
    position: absolute; left: 264px; top: 158px; width: 26px; height: 60px;
    border-radius: 13px; background: var(--accent);
  }
  .contact-pill svg { position: absolute; left: 6px; width: 14px; height: 14px; }
  .contact-pill .icon-phone { top: 9px; }
  .contact-pill .icon-mail { top: 37px; }
  .contact-list {
    position: absolute; left: 303px; top: 164px; list-style: none;
    font-family: "Poppins", sans-serif; font-size: 16px; line-height: 25px;
    color: var(--ink-light);
  }

  .abn {
    position: absolute; left: 263px; top: 293px;
    font-family: "Poppins", sans-serif; font-weight: 500; font-size: 12px;
    letter-spacing: 2.6px; color: var(--ink-light);
  }
  .abn-rule {
    position: absolute; left: 458px; right: 0; top: 301px; height: 2px;
    background: var(--accent);
  }

  .wordmark {
    position: absolute; left: 78px; top: 128px; color: var(--ink-dark);
    font-family: "Lexend", sans-serif; font-weight: 400;
  }
  .wordmark .name { display: block; font-size: 66px; line-height: 1; letter-spacing: 2px; }
  .wordmark .descriptor { display: block; margin-top: 14px; font-size: 9px; letter-spacing: 7.4px; }
</style>
</head>
<body>
<main class="canvas">
  <section class="card card--front" aria-label="Business card front">
    <div class="brand-art" role="img" aria-label="Brand artwork in blue tones"></div>
    <h1 class="person-name"><span class="first">Rowan</span> Keddle</h1>
    <p class="person-title">DIRECTOR</p>
    <div class="contact-pill" aria-hidden="true">
      <svg class="icon-phone" viewBox="0 0 24 24"><path fill="#fff" d="M6.6 10.8a15.1 15.1 0 0 0 6.6 6.6l2.2-2.2c.3-.3.7-.4 1-.2 1.1.4 2.3.6 3.6.6.6 0 1 .4 1 1V20c0 .6-.4 1-1 1A17 17 0 0 1 3 4c0-.6.4-1 1-1h3.5c.6 0 1 .4 1 1 0 1.3.2 2.5.6 3.6.1.3 0 .7-.2 1z"/></svg>
      <svg class="icon-mail" viewBox="0 0 24 24"><rect x="3" y="6" width="18" height="12" fill="none" stroke="#fff" stroke-width="2"/><path d="M3 6l9 7 9-7" fill="none" stroke="#fff" stroke-width="2"/></svg>
    </div>
    <ul class="contact-list">
      <li>0431 286 517</li>
      <li>rowan@tbk-plumbing.com.au</li>
    </ul>
    <p class="abn">ABN - 73 215 904 386</p>
    <div class="abn-rule"></div>
  </section>

  <section class="card card--back" aria-label="Business card back">
    <div class="wordmark">
      <span class="name">tbk</span>
      <span class="descriptor">plumbing services</span>
    </div>
    <div class="brand-art" role="img" aria-label="Brand artwork in blue tones"></div>
  </section>
</main>
</body>
</html>
```